Business Card Design Project

The business card is for an educational company that provides personalised tuition to students.

The company logo is in orange and blue (as provided) and should be included in the name card design

The philosophy of the company is to make learning a comfortable experience for student as such design of the namecard should look fresh and has a bit of the 'wow' factor. Some of the namecard design that appeals to me are as uploaded under Sample Design.

The particulars that need to be provided are:
(1): Company Name (Lantern Education)
(1): Name
(2): Educational qualifications which will appear below name
(3): Mobile number
(4): Email address
(5): Website

Industry/Entity Type

Business

Requirements
Must have
• (1): Company Logo

(2): The card background should preferably be coloured both for the front side and back.

(3): The choice of font is important as part of the selection consideration. There is no preferred font that I have selected, designer is free to choose the font that will complement their design.

```html
<!DOCTYPE html>
<html lang="en">
<head>
<meta charset="utf-8">
<title>Lantern Education — Business Card</title>
<link rel="stylesheet" href="https://fonts.googleapis.com/css2?family=Quicksand:wght@500;600&display=swap">
<style>
  :root {
    --canvas: #e6ebee;
    --card: #a9d5f2;
    --card-light: #bfe0f6;
    --wave: #1a93d0;
    --wave-soft: #6fbde6;
    --ink: #5a6770;
    --accent: #f08a24;
    --mark-square: #f07d1f;
  }
  * { margin: 0; padding: 0; box-sizing: border-box; }
  html, body {
    width: 1200px;
    height: 960px;
    overflow: hidden;
    background: var(--canvas);
    font-family: "Quicksand", "Trebuchet MS", sans-serif;
  }
  .sheet {
    width: 1200px;
    height: 960px;
    display: flex;
    flex-direction: column;
    align-items: center;
    justify-content: center;
    gap: 32px;
  }
  .card {
    position: relative;
    width: 760px;
    height: 434px;
    background: linear-gradient(160deg, var(--card-light), var(--card) 60%);
    overflow: hidden;
    box-shadow: 0 6px 18px rgba(40, 60, 80, 0.18);
  }
  .wave-band {
    position: absolute;
    left: 0;
    right: 0;
    bottom: 0;
    height: 46%;
    background: repeating-linear-gradient(
      180deg,
      transparent 0 22px,
      var(--wave-soft) 22px 26px,
      transparent 26px 40px
    ), linear-gradient(180deg, var(--card), #95cbee);
  }
  /* front side */
  .identity {
    position: absolute;
    left: 40px;
    top: 150px;
    color: var(--ink);
  }
  .identity__name {
    font-size: 38px;
    font-weight: 500;
    letter-spacing: 0.5px;
  }
  .identity__role {
    font-size: 25px;
    font-weight: 500;
    margin-top: 2px;
  }
  .contacts {
    position: absolute;
    left: 410px;
    top: 120px;
    list-style: none;
    color: var(--ink);
    font-size: 19px;
    font-weight: 500;
  }
  .contacts li {
    display: flex;
    align-items: center;
    gap: 12px;
    height: 30px;
  }
  .contacts svg { width: 16px; height: 16px; flex: none; }
  /* back side */
  .brand {
    position: absolute;
    left: 150px;
    top: 70px;
    display: flex;
    align-items: center;
    gap: 26px;
  }
  .brand__square {
    width: 118px;
    height: 118px;
    border-radius: 16px;
    background: var(--mark-square);
  }
  .brand__name {
    font-size: 56px;
    font-weight: 600;
    line-height: 0.95;
    color: var(--ink);
  }
  .back .wave-band { height: 42%; }
</style>
</head>
<body>
<main class="sheet">
  <section class="card front" aria-label="Card front">
    <div class="identity">
      <p class="identity__name">Marina Holloway</p>
      <p class="identity__role">Operation Manager</p>
    </div>
    <ul class="contacts">
      <li>
        <svg viewBox="0 0 16 16" aria-hidden="true"><rect x="4" y="1" width="8" height="14" rx="1.5" fill="none" stroke="var(--accent)" stroke-width="1.6"/><rect x="6" y="3" width="4" height="7" fill="var(--accent)"/></svg>
        (221) 70 482 15 36
      </li>
      <li>
        <svg viewBox="0 0 16 16" aria-hidden="true"><rect x="1" y="3" width="14" height="10" fill="none" stroke="var(--accent)" stroke-width="1.6"/><path d="M1 3 L8 9 L15 3" fill="none" stroke="var(--accent)" stroke-width="1.6"/></svg>
        name@lantern-education.com
      </li>
      <li>
        <svg viewBox="0 0 16 16" aria-hidden="true"><circle cx="8" cy="8" r="7" fill="var(--accent)"/><path d="M1 8 H15 M8 1 C5 4 5 12 8 15 M8 1 C11 4 11 12 8 15" fill="none" stroke="var(--card-light)" stroke-width="1.1"/></svg>
        www.lantern-education.com
      </li>
    </ul>
    <div class="wave-band" role="img" aria-label="Band of blue wavy lines"></div>
  </section>

  <section class="card back" aria-label="Card back">
    <div class="brand">
      <span class="brand__square"></span>
      <span class="brand__name">Lantern<br>Education</span>
    </div>
    <div class="wave-band" role="img" aria-label="Band of blue wavy lines"></div>
  </section>
</main>
</body>
</html>
```